Website Redesign - We Need Your Magic!

Hello we are looking for you to help us re-design a high end and professional website for a high-end private school.

Here is the current site: http://www.ferndalecrest.com/

NOTE THIS IS DESIGN ONLY, NO CODING :)

The image they want to portray is that of high quality sports and education, in a creative "un-stiff" way.

Menu Bar: Horizontal

Look and Feel:

Site Colors: Dark green and a Gold yellow (logos are attached)

This site will represent a school so the look must be clean, bold, and classy. The site must have a very clean user interface, with things easily recognizable. Think simple.

The site should be visually appealing! If you come to me with templates, or a ton of text you will be out.

This site should be outside the box, we do not want boring, we do not want status quo. This site should instill excitement, innovation, and athletics.

So the main points again are:

1. High-end and classy look, with creative feel
2. Simple and clear navigation style
3. To cover the Junior and High School - Ferndale Crest College Schools

Think outside the box. We look forward to seeing what you come up with!!

Thank you for helping us create an amazing site for the school!

Industry/Entity Type

School

```html
<!DOCTYPE html>
<html lang="en">
<head>
<meta charset="utf-8">
<title>Ferndale Crest College</title>
<link href="https://fonts.googleapis.com/css2?family=Arimo:ital,wght@0,400;0,700;1,700&family=Ubuntu:wght@500&display=swap" rel="stylesheet">
<style>
:root{
  --green-dark:#1d4f17;
  --green:#1f6a29;
  --green-deep:#0e4716;
  --gold:#b3890f;
  --gold-box:#c0a312;
  --gold-hi:#d8c21d;
  --text:#2b2b2b;
  --muted:#777;
  --line:#cfcfcf;
  --footer:#2b2b2b;
  --footer-base:#1c1c1c;
  --social:#4b5f86;
}
*{margin:0;padding:0;box-sizing:border-box}
html,body{width:905px;height:1200px;overflow:hidden}
body{position:relative;background:#fff;font-family:"Arimo",Arial,sans-serif;color:var(--text);font-size:10.4px;line-height:13.6px}
.abs{position:absolute}
.header{left:0;top:0;width:905px;height:120px;background:#f7f7f7}
.brand-mark{left:78px;top:18px;width:74px;height:74px;border-radius:50%;background:var(--green-dark);border:4px solid var(--gold-hi)}
.brand-name{left:171px;top:34px;font-family:"Ubuntu",sans-serif;font-weight:500;font-size:24.5px;color:var(--green-dark)}
.tagline{left:171px;top:73px;font-size:11px;color:#333}
.contact{left:528px;top:33px;font-size:11px;color:#333;display:flex;gap:14px;align-items:center}
.contact span{display:flex;align-items:center;gap:6px}
.search{left:525px;top:65px;width:238px;height:27px;border:1px solid #ddd;background:#fff;font-size:10px;color:#888;padding:7px 8px}
.search-btn{left:767px;top:65px;width:63px;height:27px;background:var(--green-dark);color:#fff;font-weight:700;font-size:9px;display:flex;align-items:center;justify-content:center;gap:4px}
.nav{left:0;top:120px;width:905px;height:34px;background:linear-gradient(var(--green),var(--green-deep));display:flex;align-items:center;padding-left:78px}
.nav a{color:#fff;font-weight:700;font-size:10.4px;text-decoration:none;height:34px;line-height:34px}
.nav a.active{background:var(--gold-hi);color:var(--green-dark);padding:0 13px;margin-right:20px}
.hero{left:0;top:154px;width:905px;height:297px;display:flex}
.hero div{height:100%}
.hero-arrow{top:272px;width:31px;height:31px;border-radius:50%;background:#1b1b1b;display:flex;align-items:center;justify-content:center}
h2{font-family:"Arimo",sans-serif;font-weight:400;color:var(--gold);font-size:18px}
.lead{color:var(--green-dark);font-weight:700;font-size:10.1px;line-height:15px}
.divider{height:1px;background:var(--line)}
.more{font-style:italic;font-weight:700;font-size:9.5px;background:#fff;padding-left:5px}
.arrows{display:flex;gap:3px}
.arrows i{width:14px;height:14px;background:#e3e3e3;border:1px solid #ccc;display:flex;align-items:center;justify-content:center}
.event-date{font-style:italic;font-weight:700;color:var(--green-dark);font-size:9.5px;text-align:right}
.newsletter{left:602px;top:485px;width:228px;height:132px;background:var(--gold-box);color:#fff}
.newsletter h3{position:absolute;left:48px;top:14px;font-size:18px;color:#111;font-weight:700;letter-spacing:.3px}
.newsletter p{position:absolute;left:16px;top:50px;width:200px;font-size:9.6px;line-height:13.6px}
.nl-input{left:16px;top:85px;width:160px;height:26px;background:#fff;color:#333;font-size:10.4px;padding:6px 7px}
.nl-go{left:176px;top:85px;width:38px;height:26px;background:var(--green-dark);color:#fff;font-size:12px;display:flex;align-items:center;justify-content:center}
.sports li{list-style:none;display:flex;align-items:center;gap:8px;height:21px;font-size:11px;color:#222}
.sports li i{width:9px;height:9px;border:1px solid #888;border-radius:50%;display:flex;align-items:center;justify-content:center}
.social-box{left:602px;top:795px;width:228px;height:247px;border:1px solid #b9b9b9;background:#fff;font-size:8.5px}
.social-head{height:24px;background:var(--social);color:#fff;display:flex;justify-content:space-between;align-items:center;padding:0 7px;font-size:9.5px}
.social-head b{font-size:11px}
.tile{background:#2f7a2f}
.social-name{color:var(--social);font-size:10px}
.faces{display:flex;gap:5px}
.faces div{width:37px;height:37px}
.footer{left:0;top:1072px;width:905px;height:102px;background:var(--footer);color:#fff}
.footer h4{font-size:12.5px;font-weight:700}
.footer .small{font-size:10px;color:#ddd}
.base{left:0;top:1174px;width:905px;height:26px;background:var(--footer-base);color:#ccc;font-size:10px;text-align:center;line-height:26px}
</style>
</head>
<body>

<div class="abs header"></div>
<div class="abs brand-mark"></div>
<div class="abs brand-name">Ferndale Crest College</div>
<div class="abs tagline">Stepping Ahead in . Eduction . Culture &nbsp;. &nbsp;Sport . &nbsp;Life</div>
<div class="abs contact">
  <span><svg width="12" height="12" viewBox="0 0 12 12"><path d="M2.5 1 L4.5 1 L5.3 3.6 L4 4.6 Q5 7 7.4 8 L8.4 6.7 L11 7.5 L11 9.5 Q10.5 11 9 11 Q1 10 1 2.5 Q1 1 2.5 1Z" fill="#222"/></svg>0770555010 / 0770555020</span>
  <span><svg width="13" height="10" viewBox="0 0 13 10"><rect width="13" height="10" fill="#e6a52a"/><path d="M0 0 L6.5 5.5 L13 0" stroke="#fff" fill="none"/></svg>admin@ferndalecrest.com</span>
</div>
<div class="abs search">Search you any keyword</div>
<div class="abs search-btn"><svg width="9" height="9" viewBox="0 0 9 9"><circle cx="3.7" cy="3.7" r="2.8" stroke="#fff" stroke-width="1.3" fill="none"/><path d="M5.8 5.8 L8.3 8.3" stroke="#fff" stroke-width="1.4"/></svg>Search</div>

<nav class="abs nav">
  <a class="active">HOME</a>
  <a style="margin-right:40px">ABOUT US</a>
  <a style="margin-right:41px">ACADEMICS</a>
  <a style="margin-right:41px">SPORTS</a>
  <a style="margin-right:41px">JOINING FERNDALE</a>
  <a style="margin-right:41px">WORKING AT THE COLLEGE</a>
  <a>CONTACT US</a>
</nav>

<div class="abs hero">
  <div role="img" aria-label="Group of smiling students standing on a lawn" style="width:300px;background:linear-gradient(160deg,#3f5a2c,#8c7a63 55%,#5d7a3a)"></div>
  <div role="img" aria-label="Mountain bike race with riders approaching on a dusty track" style="width:335px;background:linear-gradient(180deg,#9a8a76,#5f5b52 50%,#6f6a48)"></div>
  <div role="img" aria-label="Two hockey players running on a grass field" style="width:270px;background:linear-gradient(200deg,#2d5a2a,#a7a88e 45%,#56782f)"></div>
</div>
<div class="abs hero-arrow" style="left:15px"><svg width="8" height="10" viewBox="0 0 8 10"><path d="M6 1 L2 5 L6 9" stroke="#f0d21a" stroke-width="2.2" fill="none"/></svg></div>
<div class="abs hero-arrow" style="left:859px"><svg width="8" height="10" viewBox="0 0 8 10"><path d="M2 1 L6 5 L2 9" stroke="#f0d21a" stroke-width="2.2" fill="none"/></svg></div>

<h2 class="abs" style="left:75px;top:480px">Welcome to Ferndale Crest College</h2>
<p class="abs lead" style="left:77px;top:513px;width:500px">Welcome to Ferndale Crest Group of Schools where our School Motto is ‘Kunyana’ meaning Togetherness. We aim to work together in every aspect of School life, from academics to sport.</p>
<p class="abs" style="left:77px;top:556px;width:490px">Ferndale Crest College opened on 14th February 1983 and occupies 120 ha of land amidst the low hills of the Marula Range, 8km west of Kestrelton. This location encourages focus on School life away from the distractions and hustle and bustle of the larger towns.</p>
<div class="abs divider" style="left:75px;top:611px;width:485px"></div>
<div class="abs more" style="left:494px;top:605px">More Details.</div>

<h2 class="abs" style="left:75px;top:629px">Headmaster's Welcome Note</h2>
<div class="abs" role="img" aria-label="Portrait of the headmaster" style="left:77px;top:663px;width:120px;height:141px;background:linear-gradient(160deg,#3c6b4a,#b79a6a 60%,#3d5f45)"></div>
<p class="abs" style="left:211px;top:661px;width:352px"><b>Welcome to Ferndale Crest College.</b> &nbsp;Here at the College we aim to encourage each pupil to be a self-confident, well-rounded individual. &nbsp;We aim to propel them to the highest level of achievement in both academics and extra- curricular activities to provide them with the life skills they will need when they leave the College and to prepare them to be of value to society.</p>
<p class="abs" style="left:211px;top:756px;width:352px">The College is a warm community which lives out high standards and is rightly proud of its achievements. &nbsp;We are a small enough School for each pupil to be known well, but large enough to offer a wide range of subjects and experience.</p>
<div class="abs divider" style="left:75px;top:830px;width:485px"></div>
<div class="abs more" style="left:494px;top:824px">More Details.</div>

<h2 class="abs" style="left:78px;top:881px">Upcoming Events</h2>
<div class="abs arrows" style="left:268px;top:885px"><i><svg width="6" height="7"><path d="M5 0 L1 3.5 L5 7Z" fill="#5a8a2a"/></svg></i><i><svg width="6" height="7"><path d="M1 0 L5 3.5 L1 7Z" fill="#5a8a2a"/></svg></i></div>
<div class="abs divider" style="left:78px;top:909px;width:224px"></div>
<div class="abs event-date" style="left:80px;top:920px;width:213px">Mon 04 Aug</div>
<p class="abs" style="left:80px;top:936px;width:220px">When an unknown printer took a galley of type and scra mbled it specimen book.</p>
<div class="abs divider" style="left:80px;top:974px;width:213px"></div>
<div class="abs event-date" style="left:80px;top:982px;width:213px">Mon 04 Aug</div>
<p class="abs" style="left:80px;top:997px;width:220px">When an unknown printer took a galley of type and scra mbled it specimen book.</p>

<h2 class="abs" style="left:339px;top:881px">School Calender</h2>
<div class="abs arrows" style="left:534px;top:883px"><i><svg width="6" height="7"><path d="M5 0 L1 3.5 L5 7Z" fill="#5a8a2a"/></svg></i><i><svg width="6" height="7"><path d="M1 0 L5 3.5 L1 7Z" fill="#5a8a2a"/></svg></i></div>
<div class="abs divider" style="left:339px;top:909px;width:226px"></div>
<p class="abs" style="left:341px;top:919px;width:222px;line-height:15.2px">Begins: Tuesday 14th January<br>1st Fixture Free: Friday 31st January – Monday 3rd February<br>Half-Term: Thursday 20th February – Tuesday 25th February<br>2nd Fixture Free: Friday 14th March – Monday 17th March<br>Term Ends: Thursday &nbsp;10th April</p>

<div class="abs newsletter">
  <svg class="abs" style="left:14px;top:12px" width="25" height="25" viewBox="0 0 25 25"><circle cx="12.5" cy="12.5" r="12" fill="#1e6b2a"/><circle cx="12.5" cy="12.5" r="8" fill="#fff"/><rect x="8" y="9.5" width="9" height="6" fill="#1e6b2a"/><path d="M8 9.5 L12.5 13 L17 9.5" stroke="#fff" fill="none"/></svg>
  <h3>NEWSLETTER</h3>
  <p>If you would like to be added to the list of parents that receive the School Newsletter,</p>
  <div class="abs nl-input">Email Address</div>
  <div class="abs nl-go">GO</div>
</div>

<h2 class="abs" style="left:605px;top:636px">Sports Announcements</h2>
<ul class="abs sports" style="left:608px;top:667px">
  <li><i><svg width="4" height="5"><path d="M0 0 L4 2.5 L0 5Z" fill="#888"/></svg></i>Rugby</li>
  <li><i><svg width="4" height="5"><path d="M0 0 L4 2.5 L0 5Z" fill="#888"/></svg></i>Hockey Boys</li>
  <li><i><svg width="4" height="5"><path d="M0 0 L4 2.5 L0 5Z" fill="#888"/></svg></i>Soccer</li>
  <li><i><svg width="4" height="5"><path d="M0 0 L4 2.5 L0 5Z" fill="#888"/></svg></i>Hockey Girls</li>
  <li><i><svg width="4" height="5"><path d="M0 0 L4 2.5 L0 5Z" fill="#888"/></svg></i>Basketball Girls</li>
</ul>

<div class="abs social-box">
  <div class="social-head"><span>Find us on Friendspace</span><b>friendspace</b></div>
  <div class="abs tile" style="left:7px;top:32px;width:36px;height:36px"></div>
  <div class="abs social-name" style="left:45px;top:32px">Campus Chatter</div>
  <div class="abs" style="left:45px;top:49px;width:36px;height:15px;border:1px solid #ccc;background:#f2f2f2;color:#999;font-size:8px;text-align:center;line-height:13px">✓ Like</div>
  <div class="abs" style="left:85px;top:51px">You like this.</div>
  <div class="abs divider" style="left:4px;top:72px;width:218px"></div>
  <div class="abs tile" style="left:10px;top:82px;width:36px;height:36px;background:#c9c9c9"></div>
  <div class="abs social-name" style="left:52px;top:82px">Campus Chatter</div>
  <div class="abs" style="left:52px;top:97px;width:150px;font-size:9.5px;line-height:12px">"The idea of a culinary contest one either."</div>
  <div class="abs" style="left:53px;top:128px;width:140px;height:36px;border:1px solid #e3e3e3;padding:3px 6px;font-size:7.5px;line-height:10px;color:#888"><span style="color:var(--social);font-weight:700;font-size:8px">Social Media Campaign</span><br>www.campuschatter.com<br>Brightware Kitchen cookbook.</div>
  <div class="abs" style="left:211px;top:72px;width:10px;height:95px;border-left:1px solid #ddd;background:#f6f6f6"></div>
  <div class="abs" style="left:7px;top:172px">30,821 people like <b>Campus Chatter</b>.</div>
  <div class="abs faces" style="left:7px;top:186px">
    <div role="img" aria-label="Follower avatar" style="background:#8a6a55"></div>
    <div role="img" aria-label="Follower avatar" style="background:#6e5b48"></div>
    <div role="img" aria-label="Follower avatar" style="background:#8fa8c4"></div>
    <div role="img" aria-label="Follower avatar" style="background:#5b5a66"></div>
    <div role="img" aria-label="Follower avatar" style="background:#7a5140"></div>
  </div>
  <div class="abs divider" style="left:4px;top:228px;width:218px"></div>
  <div class="abs" style="left:7px;top:232px;color:#888;font-size:7.5px;display:flex;align-items:center;gap:3px"><span style="display:inline-block;width:9px;height:9px;background:var(--social)"></span>Friendspace social plugin</div>
</div>

<div class="abs footer">
  <svg class="abs" style="left:75px;top:21px" width="30" height="41" viewBox="0 0 30 41"><path d="M15 0 C6.7 0 0 6.7 0 15 C0 25 15 41 15 41 C15 41 30 25 30 15 C30 6.7 23.3 0 15 0Z" fill="#f0a424"/><circle cx="15" cy="14" r="5.5" fill="#2b2b2b"/></svg>
  <h4 class="abs" style="left:122px;top:22px">Ferndale Crest College</h4>
  <div class="abs small" style="left:122px;top:40px;width:116px;text-align:right;font-size:8px;line-height:12px">12 Acacia Lane,<br>Westbury 4021</div>
  <div class="abs small" style="left:117px;top:64px;font-size:8px;text-decoration:underline">Click here to see the directions &gt;&gt;</div>
  <h4 class="abs" style="left:310px;top:24px">Download</h4>
  <div class="abs small" style="left:310px;top:45px;line-height:16px">Registration Form<br>2nd Term 2014 Termly Calendar</div>
  <h4 class="abs" style="left:534px;top:23px">Connect With Us</h4>
  <div class="abs" style="left:534px;top:45px;width:108px;height:33px;background:#fff;border:2px solid #ccc;color:#3b4f7a;font-size:11px;line-height:12px;display:flex;align-items:center;padding-left:8px">Find us on<br>Friendspace</div>
  <div class="abs" style="left:712px;top:38px;width:80px;text-align:center;color:#777;font-size:12px;font-weight:700">Ferndale Crest</div>
</div>
<div class="abs base">Copyright © 2014 Ferndale Crest. All Rights Reserved.</div>

</body>
</html>
```